Velvet Lantern rebranding my business with a new business card

I have my new logo and now I need a refresher on my business cards. I really want something fun and fresh. I like black background or anything to make the color pop.
Logo
Name: Velvet Lantern
Contact Info as stated below:
Mira Pellow
555-013-4762
Logo
Name: Velvet Lantern
Mira Pellow
555-013-4762
hivo.me/VelvetLanternbyMira
Instagram: @VelvetLanternbyMira

Industry/Entity Type

Business

Contact Information for Business Card

double-sided. Logo on one side. Contact info on the other.

Requirements
Must have
• Logo
• Name: Velvet Lantern
• Contact Info as stated below:
• Mira Pellow
• 555-013-4762
• hivo.me/VelvetLanternbyMira
• hivo.me/VelvetLanternbyMira

```html
<!DOCTYPE html>
<html lang="en">
<head>
<meta charset="UTF-8">
<title>Velvet Lantern – Business Card</title>
<link rel="stylesheet" href="https://fonts.googleapis.com/css2?family=Source+Sans+3:wght@400;600&display=swap">
<style>
  :root {
    --backdrop: #3f3632;
    --card-black: #0c0b0b;
    --panel-black: #141313;
    --pink: #f28ca3;
    --pink-soft: #f7c6d2;
    --white: #ffffff;
    --ink-light: #e9e6e6;
  }
  * { margin: 0; padding: 0; box-sizing: border-box; }
  html, body {
    width: 1200px;
    height: 900px;
    overflow: hidden;
    background: var(--backdrop);
    font-family: "Source Sans 3", "Helvetica Neue", Arial, sans-serif;
  }
  .sheet {
    width: 1200px;
    height: 900px;
    display: flex;
    align-items: center;
    justify-content: center;
    gap: 40px;
  }
  .card {
    position: relative;
    width: 540px;
    height: 309px;
    background: var(--card-black);
    box-shadow: 0 10px 30px rgba(0,0,0,0.45);
    overflow: hidden;
  }
  .brand-disc {
    position: absolute;
    width: 146px;
    height: 146px;
    border-radius: 50%;
    background: var(--white);
    border: 2px solid var(--pink-soft);
    box-shadow: inset 0 0 0 5px var(--white), inset 0 0 0 6px var(--pink);
    display: flex;
    align-items: center;
    justify-content: center;
    text-align: center;
  }
  .brand-name {
    color: var(--pink);
    font-weight: 600;
    font-size: 22px;
    line-height: 1.1;
    width: 100px;
  }
  .card--front .brand-disc { left: 62px; top: 82px; }
  .card--back .brand-disc { left: 197px; top: 82px; }

  .contact-panel {
    position: absolute;
    left: 268px;
    top: 0;
    width: 272px;
    height: 309px;
    background: var(--panel-black);
    padding: 104px 0 0 36px;
  }
  .holder-name {
    color: var(--pink);
    font-weight: 600;
    font-size: 21px;
    letter-spacing: 0.5px;
    text-transform: uppercase;
    margin-bottom: 40px;
  }
  .contact-list { list-style: none; }
  .contact-item {
    display: flex;
    align-items: center;
    gap: 9px;
    color: var(--ink-light);
    font-size: 15px;
    margin-bottom: 8px;
    white-space: nowrap;
  }
  .contact-icon {
    width: 18px;
    height: 18px;
    border-radius: 50%;
    background: var(--pink);
    flex: none;
    display: flex;
    align-items: center;
    justify-content: center;
  }
</style>
</head>
<body>
  <main class="sheet">
    <section class="card card--front" aria-label="Business card front">
      <div class="brand-disc"><span class="brand-name">Velvet Lantern</span></div>
      <div class="contact-panel">
        <h1 class="holder-name">Mira Pellow</h1>
        <ul class="contact-list">
          <li class="contact-item">
            <span class="contact-icon">
              <svg width="11" height="11" viewBox="0 0 24 24" aria-hidden="true">
                <path fill="#0c0b0b" d="M6.6 10.8a15.1 15.1 0 0 0 6.6 6.6l2.2-2.2c.3-.3.7-.4 1-.2 1.1.4 2.3.6 3.6.6.6 0 1 .4 1 1V20c0 .6-.4 1-1 1C10.6 21 3 13.4 3 4c0-.6.4-1 1-1h3.5c.6 0 1 .4 1 1 0 1.3.2 2.5.6 3.6.1.3 0 .7-.2 1z"/>
              </svg>
            </span>
            555-013-4762
          </li>
          <li class="contact-item">
            <span class="contact-icon"></span>
            hivo.me/VelvetLanternbyMira
          </li>
        </ul>
      </div>
    </section>

    <section class="card card--back" aria-label="Business card back">
      <div class="brand-disc"><span class="brand-name">Velvet Lantern</span></div>
    </section>
  </main>
</body>
</html>
```